Stylish Business Cards Wanted

- DOUBLE SIDED Design Required -

High end, edgy cards for a corporate and personal stylist. Must include logo,
Name: Belinda Harwick
Title: Director and Stylist
telephone : +61 8 7142 5809
email: belinda@theloombriefing.example
website: theloombriefing.example
Tag: Corporate Workwear & Uniform Specialist | Personal Stylist
Would like nice icons for telephone, email, website

Target Market(s)

Businesses wanting stylish uniforms, people wanting stylish wardrobes

Industry/Entity Type

Corporate Workwear Stylist

Contact Information for Business Card

I would like black, white and gold foiling incorporated in the design - possibly a touch of the other colours on my branding guide attached Name: Belinda Harwick Title: Director and Stylist telephone : +61 8 7142 5809 email: belinda@theloombriefing.example website: theloombriefing.example Tag: Corporate Workwear & Uniform Specialist | Personal Stylist Would like nice icons for telephone, email, website

Font styles to use
Other font styles liked:
• Raleway

Colors

Designer to choose colors to be used in the design.

Requirements
Must have
• Gold foil accents

```html
<!DOCTYPE html>
<html lang="en">
<head>
<meta charset="utf-8">
<title>The Loom Briefing – Business Cards</title>
<link href="https://fonts.googleapis.com/css2?family=Roboto:wght@400;500;700&display=swap" rel="stylesheet">
<style>
  :root {
    --backdrop: #1b1b1b;
    --card: #232323;
    --gold: #e7b744;
    --white: #ffffff;
    --soft-white: #f2f2f2;
  }
  html, body {
    margin: 0;
    padding: 0;
    width: 1200px;
    height: 1059px;
    overflow: hidden;
    background: var(--backdrop);
    font-family: 'Roboto', Arial, sans-serif;
  }
  .canvas {
    position: relative;
    width: 1200px;
    height: 1059px;
  }
  .card {
    position: absolute;
    background: var(--card);
    border-radius: 18px;
    box-shadow: 0 14px 26px rgba(0,0,0,0.6);
  }
  .card--front { left: 256px; top: 89px; width: 688px; height: 390px; }
  .card--back  { left: 254px; top: 547px; width: 693px; height: 393px; }

  .brand-name {
    position: absolute;
    color: var(--white);
    font-weight: 500;
    letter-spacing: 0.04em;
    text-transform: uppercase;
    text-align: center;
    line-height: 1.15;
  }
  .card--front .brand-name {
    right: 32px;
    top: 62px;
    font-size: 26px;
  }
  .card--back .brand-name {
    left: 0; right: 0;
    top: 162px;
    font-size: 36px;
  }

  .person {
    position: absolute;
    left: 33px;
    top: 206px;
  }
  .person__name {
    margin: 0;
    color: var(--gold);
    font-size: 23px;
    font-weight: 700;
    letter-spacing: 0.01em;
    text-transform: uppercase;
  }
  .person__title {
    margin: 3px 0 0;
    color: var(--soft-white);
    font-size: 16px;
    font-weight: 400;
  }
  .divider {
    position: absolute;
    left: 33px;
    right: 32px;
    top: 271px;
    height: 1px;
    background: var(--gold);
  }
  .contacts {
    position: absolute;
    left: 33px;
    top: 287px;
    margin: 0;
    padding: 0;
    list-style: none;
  }
  .contacts li {
    display: flex;
    align-items: center;
    height: 25px;
    color: var(--soft-white);
    font-size: 16.5px;
  }
  .contacts svg {
    width: 13px;
    height: 13px;
    margin-right: 7px;
    fill: var(--gold);
  }
  .services {
    position: absolute;
    right: 32px;
    top: 287px;
    margin: 0;
    padding: 0;
    list-style: none;
    text-align: right;
  }
  .services li {
    position: relative;
    padding-right: 16px;
    color: var(--soft-white);
    font-size: 16.5px;
    line-height: 22px;
    margin-bottom: 3px;
  }
  .services li::after {
    content: "";
    position: absolute;
    right: 0;
    top: 9px;
    width: 5px;
    height: 5px;
    border-radius: 50%;
    background: var(--gold);
  }
</style>
</head>
<body>
<main class="canvas">

  <section class="card card--front" aria-label="Business card front">
    <div class="brand-name">The Loom<br>Briefing</div>

    <div class="person">
      <h1 class="person__name">Belinda Harwick</h1>
      <p class="person__title">Director and Stylist</p>
    </div>

    <div class="divider"></div>

    <ul class="contacts">
      <li>
        <svg viewBox="0 0 24 24" aria-hidden="true"><path d="M6.6 10.8a15.1 15.1 0 0 0 6.6 6.6l2.2-2.2c.3-.3.7-.4 1-.2 1.1.4 2.3.6 3.6.6.6 0 1 .4 1 1V20c0 .6-.4 1-1 1A17 17 0 0 1 3 4c0-.6.4-1 1-1h3.5c.6 0 1 .4 1 1 0 1.3.2 2.5.6 3.6.1.3 0 .7-.2 1z"/></svg>
        +61 8 7142 5809
      </li>
      <li>
        <svg viewBox="0 0 24 24" aria-hidden="true"><path d="M2 5h20v14H2z M2 5l10 8 10-8" fill="none" stroke="#e7b744" stroke-width="0"/><path d="M2 5h20L12 12.5z M2 7l10 7.5L22 7v12H2z"/></svg>
        belinda@theloombriefing.example
      </li>
      <li>
        <svg viewBox="0 0 24 24" aria-hidden="true"><circle cx="12" cy="12" r="10"/><path d="M7 6c2 1 1 3 3 4s0 3 2 4 0 4 1 5M15 4c-1 2 1 3 3 3s2 3 2 3" stroke="#232323" stroke-width="1.6" fill="none"/></svg>
        www.theloombriefing.example
      </li>
    </ul>

    <ul class="services">
      <li>Corporate Workwear &amp;<br>Uniform Specialist</li>
      <li>Personal Stylist</li>
    </ul>
  </section>

  <section class="card card--back" aria-label="Business card back">
    <div class="brand-name">The Loom<br>Briefing</div>
  </section>

</main>
</body>
</html>
```